Calvanto Group Real Estate Company business cards

New business card design, we are generally happy with the basic layout of the existing front of business card, (feel free to change) but require a head shot photo on the back side.

http://www.calvanto.com.au/

Attached logos, and existing business card

------------------------------

Target Market(s)

Real estate

Industry/Entity Type

Real Estate

Contact Information for Business Card

Standard size double sided

Font styles to use
Other font styles liked:
• Futura

Requirements
Must have
• Photo head shot on the back side
Nice to have
• yes
Should not have
• No

```html
<!DOCTYPE html>
<html lang="en">
<head>
<meta charset="utf-8">
<title>Calvanto Group – Business Cards</title>
<link href="https://fonts.googleapis.com/css2?family=Jost:wght@400;600&family=Roboto:wght@400;500&display=swap" rel="stylesheet">
<style>
  :root {
    --bg: #e4e4e6;
    --purple-dark: #2a1650;
    --purple: #3e2470;
    --purple-light: #4d2e86;
    --orange: #f0891e;
    --orange-deep: #e8700e;
    --grey-strip: #8a8790;
    --white: #ffffff;
    --text-soft: #e8e2f4;
    --photo-tone: #dfe1e6;
  }
  * { box-sizing: border-box; margin: 0; padding: 0; }
  html, body { width: 1200px; height: 1200px; overflow: hidden; background: var(--bg); }
  body { position: relative; font-family: "Roboto", Arial, sans-serif; }

  .card {
    position: absolute;
    left: 220px;
    width: 760px;
    height: 440px;
    border-radius: 26px;
    overflow: hidden;
    background: linear-gradient(160deg, var(--purple-light) 0%, var(--purple) 45%, var(--purple-dark) 100%);
    box-shadow: 0 10px 24px rgba(0,0,0,.22);
  }
  .card--front { top: 90px; }
  .card--back { top: 640px; }

  /* Front */
  .tagline {
    position: absolute;
    left: 54px;
    top: 140px;
    font-family: "Jost", sans-serif;
    font-weight: 400;
    font-size: 40px;
    line-height: 1.1;
    color: var(--text-soft);
  }
  .tagline .accent { color: var(--orange); }
  .photo {
    position: absolute;
    right: 24px;
    top: 24px;
    width: 340px;
    height: 300px;
    background: linear-gradient(180deg, #f2f3f5 0%, var(--photo-tone) 100%);
  }
  .brand {
    position: absolute;
    font-family: "Jost", sans-serif;
    font-weight: 400;
    color: var(--white);
    letter-spacing: 0.5px;
    white-space: nowrap;
    line-height: 1;
  }
  .card--front .brand { left: 54px; bottom: 48px; font-size: 50px; }

  /* Back */
  .side-band {
    position: absolute;
    left: 0; top: 0; bottom: 0;
    width: 72px;
    background: linear-gradient(180deg, var(--orange) 0%, var(--orange-deep) 100%);
  }
  .side-band::after {
    content: "";
    position: absolute;
    right: -8px; top: 0; bottom: 0;
    width: 8px;
    background: var(--grey-strip);
  }
  .card--back .brand { left: 130px; top: 76px; font-size: 72px; }
  .contact {
    position: absolute;
    left: 130px;
    top: 238px;
    color: var(--white);
    font-size: 19px;
  }
  .contact__name {
    font-family: "Jost", sans-serif;
    font-weight: 600;
    font-size: 28px;
    color: var(--orange);
    line-height: 1;
  }
  .contact__role { font-size: 15px; margin: 4px 0 16px; color: var(--text-soft); }
  .contact__row { display: flex; align-items: center; gap: 12px; height: 30px; }
  .contact__label { color: var(--orange); }
  .contact__row svg { width: 18px; height: 18px; flex: none; }
  .social {
    position: absolute;
    right: 40px;
    top: 232px;
    display: flex;
    align-items: center;
    gap: 6px;
    color: var(--white);
    font-size: 17px;
  }
  .social__label { margin-right: 6px; }
  .social__square { width: 24px; height: 24px; border-radius: 4px; background: var(--orange); }
</style>
</head>
<body>

  <section class="card card--front" aria-label="Business card front">
    <p class="tagline">Let us<br>show you<br><span class="accent">property</span></p>
    <div class="brand">calvanto group</div>
    <div class="photo" role="img" aria-label="Head shot photo of the director in a suit"></div>
  </section>

  <section class="card card--back" aria-label="Business card back">
    <div class="side-band"></div>
    <div class="brand">calvanto group</div>

    <div class="contact">
      <p class="contact__name">Daniel Tran</p>
      <p class="contact__role">Director</p>
      <p class="contact__row"><span class="contact__label">ABN:</span> 52 418 903 276</p>
      <p class="contact__row">
        <svg viewBox="0 0 18 18" aria-hidden="true"><rect x="4" y="1" width="10" height="16" rx="2" fill="none" stroke="#f0891e" stroke-width="2"/><circle cx="9" cy="14" r="1.2" fill="#f0891e"/></svg>
        0412 585 306
      </p>
      <p class="contact__row">
        <svg viewBox="0 0 18 18" aria-hidden="true"><rect x="1" y="3" width="16" height="12" rx="1.5" fill="none" stroke="#f0891e" stroke-width="2"/><path d="M1.5 4l7.5 6 7.5-6" fill="none" stroke="#f0891e" stroke-width="2"/></svg>
        daniel.tran@calvanto.com.au
      </p>
      <p class="contact__row">
        <svg viewBox="0 0 18 18" aria-hidden="true"><circle cx="9" cy="9" r="7.5" fill="none" stroke="#f0891e" stroke-width="2"/><ellipse cx="9" cy="9" rx="3.2" ry="7.5" fill="none" stroke="#f0891e" stroke-width="1.5"/><path d="M1.5 9h15" stroke="#f0891e" stroke-width="1.5"/></svg>
        calvanto.com.au
      </p>
    </div>

    <div class="social">
      <span class="social__label">Find us:</span>
      <span class="social__square"></span>
      <span class="social__square"></span>
      <span class="social__square"></span>
    </div>
  </section>

</body>
</html>
```